I am looking for a modern, clean and neat design for a reflexology and well being business. The business name is Gralo Tund (this is an old Latin word for wellbeing). The colours I would like are purple, white and grey. I am open to suggestions for pictures such as healing or working hands, a pair of feet, images that represent my business that you may think of....... or maybe you think no images at all would be best? My tag line is: "Relax, Renew, Revive" or "Find you balance......... Relax, Renew, Revive" I can decide which I want so I would like to see what both would look like. I would like space on the back to write the client's appointment date and time (more than once)

```html
<!DOCTYPE html>
<html lang="en">
<head>
<meta charset="UTF-8">
<title>Gralo Tund – Business Cards</title>
<link href="https://fonts.googleapis.com/css2?family=Open+Sans:wght@400;600;700&display=swap" rel="stylesheet">
<style>
  :root {
    --bg: #3a3a3c;
    --card: #050505;
    --white: #ffffff;
    --lavender: #a9b9e0;
    --muted: #d9d9d9;
  }
  * { margin: 0; padding: 0; box-sizing: border-box; }
  html, body { width: 1200px; height: 900px; overflow: hidden; }
  body {
    background: var(--bg);
    font-family: "Open Sans", sans-serif;
    color: var(--white);
    position: relative;
  }
  .card {
    position: absolute;
    width: 620px;
    height: 354px;
    background: var(--card);
    border-radius: 22px;
    overflow: hidden;
  }
  .card--back { left: 80px; top: 90px; }
  .card--front { left: 500px; top: 456px; }

  .brand {
    position: absolute;
    display: flex;
    align-items: center;
    gap: 10px;
    font-size: 24px;
    font-weight: 400;
    letter-spacing: 2px;
    color: var(--white);
    white-space: nowrap;
  }
  .brand__dot {
    width: 16px; height: 16px;
    border-radius: 50%;
    background: var(--lavender);
  }
  .card--back .brand { right: 46px; top: 70px; }
  .card--front .brand { right: 46px; top: 62px; }

  .tagline {
    position: absolute;
    right: 46px; top: 38px;
    font-size: 13px;
    font-weight: 600;
    letter-spacing: 1px;
  }

  .appointment {
    position: absolute;
    left: 46px; bottom: 26px;
    width: 400px;
  }
  .appointment__title {
    font-size: 20px;
    font-weight: 700;
    margin-bottom: 10px;
  }
  .appointment__row {
    display: flex;
    align-items: flex-end;
    font-size: 14px;
    line-height: 1;
    margin: 0 0 13px 18px;
  }
  .appointment__row:last-child { margin-bottom: 0; }
  .appointment__line {
    flex: 1;
    border-bottom: 2px dotted var(--muted);
    margin-left: 4px;
  }

  .contact {
    position: absolute;
    left: 46px; bottom: 74px;
  }
  .contact__name {
    font-size: 24px;
    font-weight: 700;
    letter-spacing: 1px;
    line-height: 1.1;
  }
  .contact__role {
    font-size: 13px;
    color: var(--lavender);
    letter-spacing: 1px;
    margin-bottom: 6px;
  }
  .contact__item {
    display: flex;
    align-items: center;
    gap: 8px;
    font-size: 14px;
    line-height: 1.45;
  }
  .contact__item svg { width: 11px; height: 11px; fill: var(--white); }

  .band { position: absolute; left: 0; top: 0; width: 620px; height: 354px; }
</style>
</head>
<body>

  <section class="card card--back">
    <p class="tagline">RELAX, RENEW, REVIVE</p>
    <div class="brand"><span class="brand__dot"></span>GRALO TUND</div>
    <div class="appointment">
      <h2 class="appointment__title">Appointment:</h2>
      <div class="appointment__row">Name:<span class="appointment__line"></span></div>
      <div class="appointment__row">Date:<span class="appointment__line"></span></div>
      <div class="appointment__row">Time:<span class="appointment__line"></span></div>
      <div class="appointment__row">Date:<span class="appointment__line"></span></div>
      <div class="appointment__row">Time:<span class="appointment__line"></span></div>
    </div>
  </section>

  <section class="card card--front">
    <div class="brand"><span class="brand__dot"></span>GRALO TUND</div>
    <svg class="band" viewBox="0 0 620 354" aria-hidden="true">
      <polygon points="140,322 470,286 470,354 140,354" fill="var(--white)"/>
      <polygon points="470,286 620,270 620,354 470,354" fill="var(--lavender)"/>
    </svg>
    <div class="contact">
      <h1 class="contact__name">MARA VELDEN</h1>
      <p class="contact__role">DIRECTOR</p>
      <p class="contact__item">
        <svg viewBox="0 0 24 24"><path d="M6.6 10.8a15.5 15.5 0 0 0 6.6 6.6l2.2-2.2c.3-.3.7-.4 1-.2 1.1.4 2.3.6 3.6.6.6 0 1 .4 1 1V20c0 .6-.4 1-1 1A17 17 0 0 1 3 4c0-.6.4-1 1-1h3.5c.6 0 1 .4 1 1 0 1.3.2 2.5.6 3.6.1.3 0 .7-.2 1z"/></svg>
        +330 5512-7043
      </p>
      <p class="contact__item">
        <svg viewBox="0 0 24 24"><path d="M2 5h20v14H2zm2 2v.5l8 5 8-5V7zm0 2.8V17h16V9.8l-8 5z"/></svg>
        info@gralotund.com
      </p>
      <p class="contact__item">
        <svg viewBox="0 0 24 24"><path d="M12 2a10 10 0 1 0 0 20 10 10 0 0 0 0-20zm0 2c1 1.3 1.8 3.3 2 6h-4c.2-2.7 1-4.7 2-6zM4.1 11h4c.1 1.9.5 3.7 1.1 5.2A8 8 0 0 1 4.1 11zm0-2a8 8 0 0 1 5.1-5.2C8.6 5.3 8.2 7.1 8.1 9zm7.9 11c-1-1.3-1.8-3.3-2-7h4c-.2 3.7-1 5.7-2 7zm2.8-3.8c.6-1.5 1-3.3 1.1-5.2h4a8 8 0 0 1-5.1 5.2zM15.9 9c-.1-1.9-.5-3.7-1.1-5.2A8 8 0 0 1 19.9 9z"/></svg>
        www.gralotund.com
      </p>
    </div>
  </section>

</body>
</html>
```